We need a new website design for our company Brindle Forks (https://www.brindleforks.com/). We DO NOT WANT A BORING STANDARD SITE. This site has to be different, and has to POP!

Logo Files: https://files.examplecloud.net/folders/a7Kq3Lm9Zx2Tp8Rw4Vn6Yb1Hc5Jd0Fs

Website Photos here: https://files.examplecloud.net/folders/b3Wm8Qx_T2ngVr7Lp4Ks9Hd6Zc1Ya0Ej

Websites we like:
https://morvenite.sitebloom.io/
http://crunova.com/

We will need the site building Wordpress/Woocommerce and also help with interior pages & installation plug-ins -- see further attachments.

Information about the company:
1. PURPOSE: Why do we exist?
We believe that food is the root source to healthy living.
2. VISION: What future do we want to help create?
A world of healthy and happy people.
3. MISSION: What are we here to do?
Empower every person to utilize food as a means of living a healthy life.

Value Proposition:
Brindle Forks develops new food based on the latest science to provide the human body with the proper nutrients for optimal health. Our research based foods target the key health functions that support healthy aging and active lifestyles. Since 2002, we have been innovating and designing our meals to meet the needs for healthy aging to active lifestyles. To help people perform their best, today & in the future.

Objective:
This is a nationwide issue and it's coming to the surface. Food affects people in a number of different ways. Our objective is to create an approachable and sustainable solution that can assist people with a number of ailments. The end result for all of them is feeling a feeling they haven't felt in quite some time. Feeling a refreshed you. Like water for fish, food for humans. Keep it clean and simple so you can focus on enjoying your life.

PHRASES/TAGLINES:
Empowerment Through Food
Real Food, Real Results
Nutrition Made Simple
Not Just Meal Prep, Food Science
A healthier you, delivered to your door
Increase your health and wellness baseline.
Discover the potential of healthier eating
Become the best version of you
It’s incredible what proper nutrition feels like
Taste & feel the difference. Your future self will thank you.
A healthier you is just a meal away
Life Changing results
Overwhelmed with being healthy, stops here.
Designed by doctors, approved by humans
Results Driven Healthy Eating, Delivered to you.
Become the person you deserve to be.
Enjoy the process of becoming a better you

Value Propositions:
We Educate & Empower People Through Food to Live Their Best Life
Sustainable health through proper nutrition… that’s enjoyable too.

Key Statements:
We provide satisfying meals that are nutrient dense & deliver results.
Our meals provide an easy way to enjoy an anti-inflammatory diet that's as satisfying as it is healthy.
Health, fat loss & feeling good through chef-prepared, nutrient-dense, satisfying meals delivered to your door.

PLEASE REVIEW THE ATTACHMENTS.

Industry/Entity Type

See Description & Attachments

Coding

Coded - Design and coding required

Number of Pages Required

5+ page

Font styles to use
Other font styles liked:
• See Description & Attachments

Colors
0094D4
00A9DD
6FCCEA
C7EBF8
E9F6FB
00AB8E
00BBA5
67D7C9
C6EFE9
E9F9F6

Requirements
Must have
Nice to have
Should not have

```html
<!DOCTYPE html>
<html lang="en">
<head>
<meta charset="utf-8">
<title>Brindle Forks — Eat Better, Live Better</title>
<link rel="stylesheet" href="https://fonts.googleapis.com/css2?family=Josefin+Sans:wght@300;400;600;700&family=Montserrat:wght@400;500;600;700&display=swap">
<style>
:root{
  --ocean:#0094D4;
  --ocean-deep:#00729f;
  --sky:#00A9DD;
  --sky-light:#6FCCEA;
  --sky-pale:#C7EBF8;
  --sky-mist:#E9F6FB;
  --teal:#00AB8E;
  --teal-bright:#00BBA5;
  --teal-light:#67D7C9;
  --teal-pale:#C6EFE9;
  --teal-mist:#E9F9F6;
  --ink:#2f3a40;
  --muted:#55616a;
  --card-line:#d5e9f2;
  --white:#fff;
}
*{box-sizing:border-box;margin:0;padding:0}
html,body{width:1200px;height:4428px;overflow:hidden}
body{font-family:Arial,Helvetica,sans-serif;color:var(--ink);background:var(--white);position:relative}

/* header */
.site-header{position:absolute;top:0;left:0;width:1200px;height:120px;background:var(--white);z-index:5}
.brand-badge{position:absolute;left:108px;top:-40px;width:224px;height:224px;border-radius:50%;background:var(--white);display:flex;flex-direction:column;align-items:center;justify-content:flex-end;padding-bottom:50px}
.brand-name{font-family:"Josefin Sans",sans-serif;font-weight:700;font-size:30px;line-height:1;color:var(--ocean-deep);text-align:center}
.brand-tag{font-family:Montserrat,sans-serif;font-size:11px;letter-spacing:2px;color:var(--ocean-deep);margin-top:10px;white-space:nowrap}
.header-actions{position:absolute;right:114px;top:20px;display:flex;gap:10px}
.pill{height:42px;border-radius:21px;display:flex;align-items:center;gap:8px;padding:0 20px;font-family:Montserrat,sans-serif;font-size:13px;color:var(--white)}
.pill-cart{background:var(--teal)}
.pill-cart .count{width:22px;height:22px;border-radius:50%;background:var(--white);color:var(--teal);font-weight:700;font-size:12px;display:flex;align-items:center;justify-content:center}
.pill-login{background:var(--ocean)}
.main-nav{position:absolute;right:110px;top:84px;display:flex;gap:29px;font-family:"Josefin Sans",sans-serif;font-size:19px;color:var(--ocean-deep)}
.main-nav .active{font-weight:600;color:var(--teal)}

/* hero */
.hero{position:absolute;top:120px;left:0;width:1200px;height:750px;background:radial-gradient(ellipse at 40% 60%,#0f6f7a 0%,#0a3f52 45%,#06263a 100%);display:flex;flex-direction:column;align-items:center}
.hero-title{margin-top:218px;font-family:"Josefin Sans",sans-serif;font-weight:700;font-size:96px;line-height:1;color:var(--white)}
.hero-sub{margin-top:18px;font-family:"Josefin Sans",sans-serif;font-weight:300;font-size:58px;color:var(--white);letter-spacing:1px}
.hero-btn{margin-top:20px;width:193px;height:60px;border-radius:30px;background:var(--teal-bright);color:var(--white);font-family:Montserrat,sans-serif;font-size:18px;display:flex;align-items:center;justify-content:center}
.hero-dots{position:absolute;bottom:20px;display:flex;gap:8px}
.hero-dots span{width:11px;height:11px;border-radius:50%;background:var(--white)}
.hero-dots span:nth-child(2){background:var(--sky-light)}

/* headings */
.section-title{font-family:"Josefin Sans",sans-serif;font-weight:600;font-size:42px;color:var(--ocean-deep);text-align:center;letter-spacing:1px}
.section-lede{font-size:15px;color:var(--muted);text-align:center;line-height:26px;font-weight:600;font-family:Montserrat,sans-serif}

/* welcome */
.welcome{position:absolute;top:870px;left:0;width:1200px;height:564px;background:var(--sky-mist)}
.welcome .section-title{margin-top:70px}
.welcome .section-lede{width:720px;margin:18px auto 0}
.features{position:absolute;top:236px;left:0;width:1200px}
.feature{position:absolute;width:300px;text-align:center}
.blob{width:160px;height:122px;margin:0 auto;border-radius:50% 46% 52% 44%/55% 48% 52% 45%;display:flex;align-items:center;justify-content:center}
.blob.primary{background:var(--ocean)}
.blob.accent{background:var(--teal)}
.feature h3{font-family:"Josefin Sans",sans-serif;font-weight:400;font-size:23px;color:var(--ocean-deep);margin-top:22px}
.feature p{font-size:13px;line-height:26px;color:var(--muted);margin-top:10px;padding:0 20px}

/* vision */
.vision{position:absolute;top:1434px;left:0;width:1200px;height:531px}
.vision-copy{position:absolute;left:0;top:0;width:595px;height:531px;background:linear-gradient(135deg,var(--teal) 0%,var(--teal-bright) 100%);padding:42px 50px 0 111px;color:var(--white)}
.vision-copy h2{font-family:"Josefin Sans",sans-serif;font-weight:600;font-size:40px;letter-spacing:1px}
.vision-copy .rule{width:54px;height:3px;background:var(--white);margin:14px 0 24px}
.vision-copy h3{font-family:"Josefin Sans",sans-serif;font-weight:400;font-size:24px;line-height:36px}
.vision-copy p{font-size:12.5px;line-height:26px;margin-top:18px}
.btn-primary{display:inline-flex;align-items:center;justify-content:center;background:var(--ocean);color:var(--white);font-family:Montserrat,sans-serif;font-weight:500;border-radius:30px}
.vision-copy .btn-primary{width:160px;height:54px;font-size:14px;margin-top:22px}
.vision-photo{position:absolute;left:595px;top:0;width:605px;height:531px;background:radial-gradient(circle at 55% 55%,#7fa54c 0%,#0f8fa0 38%,#4f5a60 62%,#6b7074 100%)}

/* menu */
.menu{position:absolute;top:1965px;left:0;width:1200px;height:932px}
.menu .section-title{margin-top:46px}
.menu .section-lede{margin-top:14px}
.menu-card{position:absolute;width:475px;height:165px;border:2px solid var(--card-line);border-radius:6px;padding:8px;background:var(--white)}
.menu-img{position:absolute;left:8px;top:8px;width:172px;height:145px;border-radius:6px}
.menu-info{position:absolute;left:200px;top:22px;right:18px}
.menu-info h4{font-family:Montserrat,sans-serif;font-weight:600;font-size:14.5px;color:var(--ocean)}
.menu-info .tags{font-family:Montserrat,sans-serif;font-size:12px;line-height:24px;color:#444;margin-top:12px}
.menu-info .price{font-family:Montserrat,sans-serif;font-weight:600;font-size:16px;color:var(--teal);margin-top:10px}
.menu .view-btn{position:absolute;left:501px;top:803px;width:198px;height:60px;font-size:17px}

/* banner */
.promo{position:absolute;top:2897px;left:110px;width:980px;height:297px;background:linear-gradient(120deg,var(--ocean) 0%,var(--sky) 100%);border-radius:12px;overflow:hidden}
.promo-photo{position:absolute;left:0;top:0;width:430px;height:297px;border-radius:0 50% 50% 0/0 60% 60% 0;background:radial-gradient(circle at 45% 50%,#e8a9a0 0%,#a7c47a 40%,#d9d7d2 68%,#ece9e4 100%)}
.promo-copy{position:absolute;left:494px;top:58px;color:var(--white)}
.promo-copy h2{font-family:"Josefin Sans",sans-serif;font-weight:400;font-size:34px;line-height:50px;letter-spacing:1px}
.promo-copy ul{list-style:none;margin-top:16px;font-family:"Josefin Sans",sans-serif;font-size:18px}
.promo-copy li{display:flex;align-items:center;gap:14px;height:36px}

/* audience */
.audience{position:absolute;top:3194px;left:0;width:1200px;height:514px;background:var(--teal-mist)}
.audience .section-title{margin-top:74px}
.audience .section-lede{margin-top:14px}
.persona{position:absolute;top:198px;width:220px;text-align:center}
.persona .ring{width:132px;height:132px;border-radius:50%;margin:0 auto;display:flex;align-items:center;justify-content:center}
.persona .ring.primary{background:var(--ocean)}
.persona .ring.accent{background:var(--teal)}
.persona h3{font-family:"Josefin Sans",sans-serif;font-weight:400;font-size:20px;color:var(--ink);margin-top:26px;letter-spacing:.5px}
.persona p{font-size:13px;line-height:26px;color:var(--muted);margin-top:8px;padding:0 8px}

/* newsletter */
.newsletter{position:absolute;top:3708px;left:0;width:1200px;height:394px;background:linear-gradient(135deg,#064a5e 0%,#0a6f6a 35%,#0b5a7c 65%,#073a52 100%);text-align:center;color:var(--white)}
.newsletter h2{font-family:"Josefin Sans",sans-serif;font-weight:400;font-size:42px;margin-top:106px}
.newsletter p{font-family:Montserrat,sans-serif;font-size:15px;margin-top:14px}
.signup{position:absolute;left:210px;top:210px;width:758px;height:58px;border-radius:29px;background:var(--white);display:flex;overflow:hidden}
.signup span{flex:1;text-align:left;padding-left:26px;line-height:58px;font-family:"Josefin Sans",sans-serif;font-size:16px;color:#444}
.signup b{width:128px;background:var(--teal);color:var(--white);line-height:58px;font-family:Montserrat,sans-serif;font-weight:500;font-size:16px}

/* footer */
.site-footer{position:absolute;top:4102px;left:0;width:1200px;height:326px;background:var(--ocean-deep);color:var(--white)}
.footer-brand{position:absolute;left:120px;top:60px;width:280px;text-align:center}
.footer-brand .brand-name{color:var(--white);font-size:34px;line-height:40px}
.footer-brand .brand-tag{color:var(--white);font-size:12px;letter-spacing:4px;margin-top:18px}
.footer-col{position:absolute;top:62px;list-style:none;font-family:Montserrat,sans-serif;font-weight:600;font-size:13px}
.footer-col li{height:33px}
.copyright{position:absolute;left:0;right:0;top:282px;text-align:center;font-family:Montserrat,sans-serif;font-weight:500;font-size:13px}
</style>
</head>
<body>

<header class="site-header">
  <div class="brand-badge">
    <div class="brand-name">Brindle<br>Forks</div>
    <div class="brand-tag">EAT BETTER. LIVE BETTER</div>
  </div>
  <div class="header-actions">
    <div class="pill pill-cart">
      <svg width="14" height="13" viewBox="0 0 14 13"><path d="M0 1h2.5l2 7h7l2-5H4" fill="none" stroke="#fff" stroke-width="1.6"/><circle cx="5.5" cy="11" r="1.2" fill="#fff"/><circle cx="10.5" cy="11" r="1.2" fill="#fff"/></svg>
      CART ITEMS <span class="count">0</span>
    </div>
    <div class="pill pill-login">
      <svg width="11" height="13" viewBox="0 0 11 13"><rect x="0" y="5.5" width="11" height="7.5" rx="1" fill="#fff"/><path d="M2.5 6V4a3 3 0 0 1 6 0v2" fill="none" stroke="#fff" stroke-width="1.6"/></svg>
      LOGIN
    </div>
  </div>
  <nav class="main-nav">
    <span class="active">Home</span><span>About</span><span>Menu</span><span>Programs</span><span>FAQ</span><span>Contact Us</span>
  </nav>
</header>

<section class="hero">
  <div role="img" aria-label="Overhead photo of a fresh salad bowl with tomatoes, cucumber and seeds on dark stone" style="position:absolute;inset:0"></div>
  <h1 class="hero-title" style="position:relative">Brindle Forks</h1>
  <div class="hero-sub" style="position:relative">EAT BETTER LIVE BETTER</div>
  <div class="hero-btn" style="position:relative">GET STARTED</div>
  <div class="hero-dots"><span></span><span></span><span></span></div>
</section>

<section class="welcome">
  <h2 class="section-title">Welcome to Brindle Forks</h2>
  <p class="section-lede">More than just a meal plan, we provide a sustainable diet &amp; nutritional support that empowers you to live your best life, no matter your health goals.</p>
  <div class="features">
    <div class="feature" style="left:122px">
      <div class="blob primary">
        <svg width="74" height="74" viewBox="0 0 74 74" fill="none" stroke="#fff" stroke-width="3"><ellipse cx="37" cy="37" rx="32" ry="12"/><ellipse cx="37" cy="37" rx="32" ry="12" transform="rotate(60 37 37)"/><ellipse cx="37" cy="37" rx="32" ry="12" transform="rotate(-60 37 37)"/><circle cx="37" cy="37" r="4" fill="#fff"/></svg>
      </div>
      <h3>Science Backed</h3>
      <p>We are proud to say that Brindle Forks is MUCH MORE than a Healthy Food, Home Business Delivery Service.</p>
    </div>
    <div class="feature" style="left:450px">
      <div class="blob accent">
        <svg width="66" height="74" viewBox="0 0 66 74" fill="none" stroke="#fff" stroke-width="3"><path d="M14 42C4 40 2 26 12 22c0-12 16-16 21-8 5-8 21-4 21 8 10 4 8 18-2 20v28H14z"/><path d="M14 56h38M24 56v14M33 56v14M42 56v14"/></svg>
      </div>
      <h3>Chef Prepared Meals</h3>
      <p>We are proud to say that Brindle Forks is MUCH MORE than a Healthy Food, Home Business Delivery Service.</p>
    </div>
    <div class="feature" style="left:778px">
      <div class="blob primary">
        <svg width="84" height="66" viewBox="0 0 84 66" fill="none" stroke="#fff" stroke-width="3"><rect x="4" y="18" width="48" height="34" rx="3"/><path d="M52 28h16l12 12v12H52"/><circle cx="20" cy="56" r="6"/><circle cx="66" cy="56" r="6"/><circle cx="22" cy="16" r="13" fill="#0094D4"/><path d="M16 16l5 5 8-9"/></svg>
      </div>
      <h3>Delivered Fresh</h3>
      <p>We are proud to say that Brindle Forks is MUCH MORE than a Healthy Food, Home Business Delivery Service.</p>
    </div>
  </div>
</section>

<section class="vision">
  <div class="vision-copy">
    <h2>Our Vision &amp; Mission</h2>
    <div class="rule"></div>
    <h3>Educate &amp; Empower People Through<br>Food To Live Their Best Life.</h3>
    <p>Eating properly is no longer difficult. We've handcrafted delicious meals that are results driven, so all you need to do is, enjoy.No matter your situation, we can help. Our dietician designed meals focus on an anti inflammatory diet, which is the foundation to good health.</p>
    <p>No matter your situation, we can help. Our dietician designed meals focus on an anti-inflammatory diet, which is the foundation....</p>
    <span class="btn-primary">READ MORE</span>
  </div>
  <div class="vision-photo" role="img" aria-label="Teal bowl with tofu, quinoa, avocado, greens and sweet potato"></div>
</section>

<section class="menu">
  <h2 class="section-title">Our Menu</h2>
  <p class="section-lede">More than just a meal plan, we provide a sustainable diet &amp; nutritional support</p>

  <article class="menu-card" style="left:110px;top:180px">
    <div class="menu-img" role="img" aria-label="Chicken quinoa bowl" style="background:linear-gradient(135deg,#b49a6e,#7d6a48)"></div>
    <div class="menu-info"><h4>CHICKEN QUINOA BOWL</h4><div class="tags">Cal 477 | Gluten Free | No Antibiotics | No Hormones | All Natural</div><div class="price">$13.00</div></div>
  </article>
  <article class="menu-card" style="left:614px;top:180px">
    <div class="menu-img" role="img" aria-label="Chicken Greek salad" style="background:linear-gradient(135deg,#3d5a2a,#2c2a26)"></div>
    <div class="menu-info"><h4>CHICKEN GREEK SALAD</h4><div class="tags">Cal 312 | Gluten Free | No Antibiotics | No Hormones | All Natural</div><div class="price">$12.50</div></div>
  </article>
  <article class="menu-card" style="left:110px;top:381px">
    <div class="menu-img" role="img" aria-label="Spinach and feta stuffed chicken" style="background:linear-gradient(135deg,#c9a98c,#6a4a3a)"></div>
    <div class="menu-info"><h4>SPINACH AND FETA STUFFED</h4><div class="tags">Cal 611 | Gluten Free | No Antibiotics | No Hormones | All Natural</div><div class="price">$13.00</div></div>
  </article>
  <article class="menu-card" style="left:614px;top:381px">
    <div class="menu-img" role="img" aria-label="Chicken blueberry goat cheese salad" style="background:linear-gradient(135deg,#9a8a6a,#3e3a3c)"></div>
    <div class="menu-info"><h4>CHICKEN BLUEBERRY GOAT</h4><div class="tags">Cal 296 | Gluten Free | Low Carb | Antioxidant Rich</div><div class="price">$13.00</div></div>
  </article>
  <article class="menu-card" style="left:110px;top:586px">
    <div class="menu-img" role="img" aria-label="Mediterranean tuna salad" style="background:linear-gradient(135deg,#d8b48c,#b44a3a)"></div>
    <div class="menu-info"><h4>MEDITERRANEAN TUNA</h4><div class="tags">Cal 177 | Gluten Free | Low Carb | Low Calorie</div><div class="price">$13.00</div></div>
  </article>
  <article class="menu-card" style="left:614px;top:586px">
    <div class="menu-img" role="img" aria-label="Lemon caper salmon with greens" style="background:linear-gradient(135deg,#7a5a3a,#c9803e)"></div>
    <div class="menu-info"><h4>LEMON CAPER SALMON</h4><div class="tags">Cal 465 | Wild Alaskan | No Color Added | Gluten Free</div><div class="price">$14.00</div></div>
  </article>

  <span class="btn-primary view-btn">VIEW MENU</span>
</section>

<section class="promo">
  <div class="promo-photo" role="img" aria-label="Plate of ham, boiled eggs, avocado and lettuce"></div>
  <div class="promo-copy">
    <h2>Enjoy the Process of<br>Becoming a Better You!</h2>
    <ul>
      <li><svg width="16" height="16" viewBox="0 0 16 16" fill="none" stroke="#fff" stroke-width="1.3"><circle cx="8" cy="8" r="7"/><path d="M5 8h6M8.5 5.5L11 8l-2.5 2.5"/></svg>Fresh Meals Delivered Weekly</li>
      <li><svg width="16" height="16" viewBox="0 0 16 16" fill="none" stroke="#fff" stroke-width="1.3"><circle cx="8" cy="8" r="7"/><path d="M5 8h6M8.5 5.5L11 8l-2.5 2.5"/></svg>Life Changing Results</li>
    </ul>
  </div>
</section>

<section class="audience">
  <h2 class="section-title">Who is Brindle Forks For?</h2>
  <p class="section-lede">More than just a meal plan, we provide a sustainable diet &amp; nutritional support</p>
  <div class="persona" style="left:125px">
    <div class="ring primary"><svg width="70" height="64" viewBox="0 0 70 64" fill="none" stroke="#fff" stroke-width="2.6"><path d="M35 40C20 30 14 22 14 15a10 10 0 0 1 21-4 10 10 0 0 1 21 4c0 7-6 15-21 25z"/><path d="M35 16v12M29 22h12"/><path d="M4 50l12-8h14a4 4 0 0 1 0 8H22M30 50l20-10a4 4 0 0 1 4 6L34 60H8"/></svg></div>
    <h3>General Health</h3>
    <p>You need the support of a healthy diet to get back in your overall health.</p>
  </div>
  <div class="persona" style="left:369px">
    <div class="ring accent"><svg width="70" height="70" viewBox="0 0 70 70" fill="none" stroke="#fff" stroke-width="2.6"><g transform="rotate(-45 35 35)"><rect x="6" y="24" width="8" height="22" rx="2"/><rect x="15" y="20" width="8" height="30" rx="2"/><rect x="47" y="20" width="8" height="30" rx="2"/><rect x="56" y="24" width="8" height="22" rx="2"/><path d="M23 35h24"/></g></svg></div>
    <h3>Fitness Enthusiasts</h3>
    <p>You eat clean, fitness &amp; eating right are a huge part of your healthy meal delivery</p>
  </div>
  <div class="persona" style="left:613px">
    <div class="ring primary"><svg width="70" height="66" viewBox="0 0 70 66" fill="none" stroke="#fff" stroke-width="2.6"><rect x="27" y="4" width="16" height="14"/><rect x="6" y="46" width="16" height="14"/><rect x="27" y="46" width="16" height="14"/><rect x="48" y="46" width="16" height="14"/><path d="M35 18v28M14 46V34h42v12"/></svg></div>
    <h3>Business Individuals</h3>
    <p>You have a growing to-do list that never seems to end. No to do healthy meal prep.</p>
  </div>
  <div class="persona" style="left:857px">
    <div class="ring accent"><svg width="70" height="70" viewBox="0 0 70 70" fill="none" stroke="#fff" stroke-width="3"><path d="M10 40h18l8-14 8 24 6-10h10"/></svg></div>
    <h3>Professional Athletes</h3>
    <p>You refuse to accept anything less than the best when it to nutrition, Increasing</p>
  </div>
</section>

<section class="newsletter">
  <div role="img" aria-label="Assorted fresh fruit, vegetables and nuts" style="position:absolute;inset:0;background:rgba(0,0,0,.15)"></div>
  <h2 style="position:relative">Join Our Newsletter</h2>
  <p style="position:relative">More than just a meal plan, we provide a sustainable diet &amp; nutritional support</p>
  <div class="signup"><span>Enter Your Email :</span><b>SUBMIT</b></div>
</section>

<footer class="site-footer">
  <div class="footer-brand">
    <div class="brand-name">Brindle<br>Forks</div>
    <div class="brand-tag">EAT BETTER. LIVE BETTER.</div>
  </div>
  <ul class="footer-col" style="left:464px"><li>My Account</li><li>Site Help</li><li>Shipping &amp; Returns</li><li>All Products</li><li>Gift Certificates</li></ul>
  <ul class="footer-col" style="left:696px"><li>View Cart</li><li>About Us</li><li>Corporate Catering</li><li>Podcast</li><li>Become an Affiliate</li></ul>
  <ul class="footer-col" style="left:946px"><li>Order Status</li><li>Contact Us</li><li>Privacy Policy</li><li>Testimonials</li></ul>
  <div class="copyright">© Copyright 2022 Brindle Forks. All Rights Reserved</div>
</footer>

</body>
</html>
```